Business cards for Harbourline Supply Pty Ltd that import building products into Australia from China
Target Market(s)
Business to Business
Industry/Entity Type
Business
Contact Information for Business Card
Front: Logo and Business Name
Rear:
Desmond Varrick
General Manager
Mobile: 0427 561 394
email: dessie@harbourlinesupply.com.au
alternative email: dessie@outbackworks.com.au
web: www.harbourlinesupply.com.au
Adelaide, Brisbane and Darwin
Colors
ec1f27
fbee3d

```html
<!DOCTYPE html>
<html lang="en">
<head>
<meta charset="utf-8">
<title>Harbourline Supply Pty Ltd — Business Cards</title>
<link rel="stylesheet" href="https://fonts.googleapis.com/css2?family=Open+Sans:wght@400;600;700;800&display=swap">
<style>
  :root {
    --brand-red: #ec1f27;
    --brand-yellow: #fbee3d;
    --ink: #231f20;
    --card-black: #222222;
    --paper: #ffffff;
    --backdrop: #ecebe8;
  }
  * { box-sizing: border-box; margin: 0; padding: 0; }
  html, body {
    width: 1200px; height: 900px; overflow: hidden;
    background: var(--backdrop);
    font-family: "Open Sans", Arial, sans-serif;
  }
  .canvas { position: relative; width: 1200px; height: 900px; }

  .card {
    position: absolute; left: 260px; width: 680px; height: 416px;
    overflow: hidden;
    box-shadow: 0 6px 18px rgba(0,0,0,0.18);
  }

  /* Front */
  .card--front { top: 24px; background: var(--card-black); }
  .wordmark {
    position: absolute; display: flex; align-items: center; gap: 16px;
    font-weight: 800; letter-spacing: -0.5px;
  }
  .wordmark__mark { flex: none; background: var(--brand-red); }
  .card--front .wordmark {
    left: 0; right: 0; top: 170px; justify-content: center;
    color: var(--paper); font-size: 40px;
  }
  .card--front .wordmark__mark { width: 40px; height: 40px; }

  /* Back */
  .card--back { top: 460px; background: var(--paper); }
  .card__accent-area {
    position: absolute; left: 0; right: 0; bottom: 0; height: 130px;
    background: linear-gradient(100deg, var(--brand-yellow) 0%, var(--brand-red) 45%, var(--brand-red) 100%);
  }
  .card--back .wordmark {
    left: 48px; top: 150px; width: 290px;
    color: var(--ink); font-size: 27px; line-height: 1.1;
  }
  .card--back .wordmark__mark { width: 28px; height: 28px; }

  .person { position: absolute; left: 352px; top: 52px; }
  .person__name {
    font-weight: 800; font-size: 19px; letter-spacing: 0.3px;
    color: var(--ink); text-transform: uppercase;
  }
  .person__surname { color: var(--brand-red); }
  .person__role { font-size: 13px; color: var(--ink); margin-top: 1px; }

  .contact-list {
    position: absolute; left: 372px; top: 122px; list-style: none;
  }
  .contact-list li {
    display: flex; align-items: center; gap: 10px;
    font-size: 13.5px; color: var(--ink); line-height: 21px;
  }
  .contact-list svg { width: 12px; height: 12px; flex: none; fill: var(--brand-red); }

  .locations {
    position: absolute; right: 34px; top: 310px;
    font-size: 14px; color: var(--paper);
  }
</style>
</head>
<body>
<main class="canvas">

  <section class="card card--front" aria-label="Card front">
    <div class="wordmark">
      <span class="wordmark__mark"></span>
      <span class="wordmark__name">Harbourline Supply Pty Ltd</span>
    </div>
  </section>

  <section class="card card--back" aria-label="Card back">
    <div class="card__accent-area" role="img" aria-label="Decorative red and yellow accent band"></div>

    <div class="wordmark">
      <span class="wordmark__mark"></span>
      <span class="wordmark__name">Harbourline Supply Pty Ltd</span>
    </div>

    <div class="person">
      <p class="person__name">Desmond <span class="person__surname">Varrick</span></p>
      <p class="person__role">General Manager</p>
    </div>

    <ul class="contact-list">
      <li>
        <svg viewBox="0 0 12 12" aria-label="Mobile"><path d="M3 0h6a1 1 0 0 1 1 1v10a1 1 0 0 1-1 1H3a1 1 0 0 1-1-1V1a1 1 0 0 1 1-1zm0 1.5v8h6v-8z"/></svg>
        0427 561 394
      </li>
      <li>
        <svg viewBox="0 0 12 12" aria-label="Email"><path d="M0 2h12v8H0z M1 3v.3l5 3.2 5-3.2V3z" fill-rule="evenodd"/></svg>
        dessie@harbourlinesupply.com.au
      </li>
      <li>
        <svg viewBox="0 0 12 12" aria-label="Alternative email"><path d="M0 2h12v8H0z M1 3v.3l5 3.2 5-3.2V3z" fill-rule="evenodd"/></svg>
        dessie@outbackworks.com.au
      </li>
      <li>
        <svg viewBox="0 0 12 12" aria-label="Website"><circle cx="6" cy="6" r="6"/></svg>
        www.harbourlinesupply.com.au
      </li>
    </ul>

    <p class="locations">Adelaide, Brisbane and Darwin</p>
  </section>

</main>
</body>
</html>
```